Home Staging Company needs business card design

We're a home staging company called Brightly Settled Home Staging. We would like a business card design that includes aqua and gray. Our current logo of house within chair is fine but I find we almost always use the logo in one color. I'll upload images of front and back of our current card and our logo. Note that we have dropped "Solutions" from our company name and don't want to include it on the card.

Target Market(s)

Realtors and homeowners - people interested in selling their homes

Contact Information for Business Card

Marisol Thistlewood
Brightly Settled Home Staging
757-555-0193
www.brightlysettled.com
marisol@brightlysettled.com

Font styles to use
Serif
Script

Requirements
Must have
• My logo and contact details
• UPDATE***
• I forgot to say that the company name should be included on the front of the card somehow.

```html
<!DOCTYPE html>
<html lang="en">
<head>
<meta charset="utf-8">
<title>Brightly Settled Home Staging – Business Card</title>
<link rel="stylesheet" href="https://fonts.googleapis.com/css2?family=Playfair+Display:wght@400&family=Roboto:wght@400&family=Roboto+Condensed:wght@400&display=swap">
<style>
  :root {
    --backdrop: #c4c4c4;
    --aqua-light: #52b3bd;
    --aqua-deep: #1c86ad;
    --aqua-accent: #3aa5b5;
    --ink: #3a3a3a;
    --ink-soft: #555555;
    --paper-top: #f6f6f6;
    --paper-bottom: #e6e6e6;
    --white: #ffffff;
  }
  * { margin: 0; padding: 0; box-sizing: border-box; }
  html, body { width: 1200px; height: 576px; overflow: hidden; }
  body { background: var(--backdrop); position: relative; font-family: "Roboto", sans-serif; }

  .card {
    position: absolute;
    top: 138px;
    border-radius: 12px;
    box-shadow: 0 3px 6px rgba(0,0,0,0.25);
    overflow: hidden;
  }

  /* Front */
  .card-front {
    left: 82px; width: 484px; height: 294px;
    background: linear-gradient(180deg, var(--aqua-light) 0%, var(--aqua-deep) 100%);
    color: var(--white);
  }
  .front-name {
    position: absolute; left: 0; right: 0; top: 100px;
    text-align: center;
    font-family: "Playfair Display", serif; font-weight: 400;
    color: var(--white);
  }
  .front-name .name-main { display: block; font-size: 44px; line-height: 1.1; }
  .front-name .name-sub { display: block; font-size: 17px; letter-spacing: 0.42em; margin-top: 8px; padding-left: 0.42em; }
  .front-url {
    position: absolute; left: 0; right: 0; top: 268px;
    text-align: center; font-size: 13px; letter-spacing: 0.02em;
  }

  /* Back */
  .card-back {
    left: 602px; width: 480px; height: 292px;
    background: linear-gradient(180deg, var(--paper-top) 0%, var(--paper-bottom) 100%);
    color: var(--ink);
  }
  .edge-accent {
    position: absolute; left: -22px; top: 48px;
    width: 30px; height: 46px; border-radius: 50%;
    background: var(--aqua-accent);
  }
  .person { position: absolute; left: 23px; top: 48px; }
  .person-name { font-family: "Roboto Condensed", sans-serif; font-size: 20px; color: var(--ink); }
  .person-name .surname { color: var(--aqua-accent); }
  .person-title { font-size: 12px; color: var(--ink-soft); margin-top: 5px; }

  .brand {
    position: absolute; right: 22px; top: 50px;
    display: flex; align-items: center; gap: 10px;
  }
  .brand-dot { width: 34px; height: 34px; border-radius: 50%; background: var(--aqua-accent); }
  .brand-name {
    font-family: "Playfair Display", serif; font-weight: 400;
    color: var(--ink); line-height: 1.1;
  }
  .brand-name .name-main { display: block; font-size: 21px; }
  .brand-name .name-sub { display: block; font-size: 10px; letter-spacing: 0.38em; margin-top: 3px; }

  .contacts { position: absolute; left: 29px; top: 206px; list-style: none; }
  .contacts li { display: flex; align-items: center; height: 17px; margin-bottom: 0.5px; font-size: 13px; color: var(--ink); }
  .contacts svg { width: 11px; height: 11px; margin-right: 8px; fill: var(--aqua-accent); }
</style>
</head>
<body>

  <section class="card card-front" aria-label="Card front">
    <h1 class="front-name">
      <span class="name-main">Brightly Settled</span>
      <span class="name-sub">HOME STAGING</span>
    </h1>
    <p class="front-url">www.brightlysettled.com</p>
  </section>

  <section class="card card-back" aria-label="Card back">
    <span class="edge-accent"></span>
    <div class="person">
      <h2 class="person-name">Marisol <span class="surname">Thistlewood</span></h2>
      <p class="person-title">Managing Director</p>
    </div>
    <div class="brand">
      <span class="brand-dot"></span>
      <p class="brand-name">
        <span class="name-main">Brightly Settled</span>
        <span class="name-sub">HOME STAGING</span>
      </p>
    </div>
    <ul class="contacts">
      <li>
        <svg viewBox="0 0 12 12" aria-hidden="true"><path d="M1 4c0-2 1.5-3 5-3s5 1 5 3v1H8.5V3.8h-5V5H1zM3 6h6l1.5 5h-9z"/></svg>
        757-555-0193
      </li>
      <li>
        <svg viewBox="0 0 12 12" aria-hidden="true"><path d="M6 0.5a5.5 5.5 0 1 0 0 11a5.5 5.5 0 1 0 0-11zm0 1.2c.7.8 1.2 2 1.3 3.6H4.7C4.8 3.7 5.3 2.5 6 1.7zM4.7 6.5h2.6c-.1 1.6-.6 2.8-1.3 3.6-.7-.8-1.2-2-1.3-3.6zM1.8 5.3c.2-1.5 1.2-2.7 2.5-3.3-.5.9-.8 2-.8 3.3zm0 1.2h1.7c0 1.3.3 2.4.8 3.3-1.3-.6-2.3-1.8-2.5-3.3zm6.7 0h1.7c-.2 1.5-1.2 2.7-2.5 3.3.5-.9.8-2 .8-3.3zm0-1.2c0-1.3-.3-2.4-.8-3.3 1.3.6 2.3 1.8 2.5 3.3z"/></svg>
        www.brightlysettled.com
      </li>
      <li>
        <svg viewBox="0 0 12 12" aria-hidden="true"><path d="M0.5 2h11v8h-11zm1.3 1.1L6 6.3l4.2-3.2zm-.2 1.2v4.6h8.8V4.3L6 7.6z"/></svg>
        marisol@brightlysettled.com
      </li>
    </ul>
  </section>

</body>
</html>
```